BrivoNest Learning App for Children with Dyslexia

Project Description:

We are seeking a talented UI/UX designer to create engaging and intuitive designs for Brivonest, an innovative educational app designed to help children learn letters and words through a multisensory learning approach. The app aims to be particularly helpful for children with dyslexia, providing a supportive and interactive learning environment.

Key App Features & Design Requirements:

Account Creation Screen: Design a welcoming and straightforward sign-up page that allows users to register with their email or continue with Quarnix. The design should be clean, focusing on user-friendliness and accessibility, adhering to our terms of service and privacy policy.

Main Screen Design: The main screen should allocate at least 4/6 of its height to the interactive drawing area. It needs to display word prompts in both correct and scrambled orders and include options to "Show all Words," "Play all words," and a search function. The interface should be vibrant, engaging, and easy to navigate for children.

Profile Section: Create a user-friendly profile page that allows users to edit their profile image, name, username, email, links, and bio. The design should be clean and encourage user engagement.

BrivoTally Page: This section will display the user's learning progress, including rankings, a learning curve, and recently learned words. It should visually represent progress in a motivating and understandable way, suitable for a younger audience.

Visual and Auditory Feedback Implementation: Incorporate elements that support visual and auditory feedback, using dyslexia-friendly formats. This includes choosing appropriate colors, fonts, and auditory cues.

Accessibility and Customization Settings: Designs should include settings for adjusting visual contrast, font size, and the word list to accommodate individual preferences and needs.

Feel free to add more interactions and/or pages.

Design preferences:

Color Scheme: Use a bright, inviting color palette that stimulates learning and engagement without overwhelming the users.
Font Selection: Opt for fonts that are readable and accessible, particularly for users with dyslexia.
Icons and Graphics: Design custom icons and graphics that are cohesive with the app's theme and purpose. Illustrations should be simple, relatable, and supportive of the learning process.

Target Market(s)

Educational

Industry/Entity Type

Educational

Colors
0054AA
0677BA
7BADD7
CADEEF
E8F1F8
0094D4
00A9DD
6FCCEA
C7EBF8
E9F6FB

Requirements
Must have
• Educational app, a writing area, scoring and account management
Nice to have
• Statistics, Ranking Page, Settings and some nice visual features

```html
<!DOCTYPE html>
<html lang="en">
<head>
<meta charset="utf-8">
<title>Brivonest – App Screens</title>
<link href="https://fonts.googleapis.com/css2?family=Poppins:wght@400;500;600;700&family=Comic+Neue:wght@700&display=swap" rel="stylesheet">
<style>
  :root{
    --green:#6ccd00; --green-dark:#56b300; --green-light:#8fe21e;
    --orange:#ff7d12; --orange-2:#ff9a0e; --orange-btn:#ff6a00;
    --blue:#6cbdf5; --blue-2:#33acef; --blue-line:#2f9be3;
    --purple:#a653f6; --purple-2:#c27cfb; --purple-soft:#e2c6fc;
    --cyan:#38c8f5; --yellow:#ffbf0f; --red:#f05757; --violet:#9a4fd0;
    --ink:#222; --navy:#0f1f4b; --grey:#777; --field:#f0f0f0; --white:#fff;
    --head:'Comic Neue', cursive; --body:'Poppins', sans-serif;
  }
  *{box-sizing:border-box;margin:0;padding:0}
  html,body{width:1200px;height:646px;overflow:hidden;background:#fff}
  body{position:relative;font-family:var(--body);color:var(--ink)}
  .board-label{position:absolute;top:66px;width:214px;text-align:center;font-size:19px;font-weight:400;color:#222}
  .screen{position:absolute;top:107px;width:214px;height:470px;border-radius:28px;overflow:hidden}
  .screen > *{position:absolute}
  .status-time{left:9px;top:22px;font-size:11px;color:#222}
  .status-icons{right:8px;top:24px;width:40px;height:10px}
  .app-bar{left:0;top:0;width:214px;height:71px}
  .app-title{left:0;top:40px;width:214px;text-align:center;font-family:var(--head);font-weight:700;font-size:15px;color:var(--white)}
  .frame{left:4px;top:83px;width:204px;height:362px;border:2px solid rgba(255,255,255,.85);border-radius:6px}
  .card{background:var(--white);border-radius:4px}
  .center{text-align:center}

  /* Login */
  .login{left:87px;background:var(--green)}
  .login .frame{top:40px;height:408px;left:5px;width:203px}
  .login .panel{left:11px;top:47px;width:191px;height:391px}
  .brand{left:11px;top:66px;width:191px;font-family:var(--head);font-weight:700;font-size:22px;color:#111;text-align:center}
  .tagline{left:11px;top:91px;width:191px;font-size:7.5px;text-align:center}
  .hero{left:14px;top:113px;width:186px;height:124px;border-radius:4px;background:radial-gradient(ellipse at 50% 40%,#b07a4c 0 28%,#cbe8b5 55%,#eaf6df 80%)}
  .create{left:11px;top:248px;width:191px;text-align:center;font-family:var(--head);font-weight:700;font-size:16px;color:var(--navy)}
  .create-sub{left:11px;top:271px;width:191px;text-align:center;font-size:7.5px;color:#444}
  .field{left:16px;top:290px;width:180px;height:27px;border-radius:4px;background:var(--field);font-size:7.5px;color:#555;padding:9px 10px}
  .btn-primary{left:16px;top:321px;width:180px;height:27px;border-radius:4px;background:linear-gradient(var(--green-light),var(--green-dark));color:#fff;font-family:var(--head);font-weight:700;font-size:9px;text-align:center;line-height:27px}
  .or{left:11px;top:356px;width:191px;text-align:center;font-size:7.5px;color:#444}
  .btn-alt{left:16px;top:374px;width:180px;height:27px;border-radius:4px;background:var(--field);font-family:var(--head);font-weight:700;font-size:9px;display:flex;align-items:center;justify-content:center;gap:6px}
  .btn-alt .mark{width:10px;height:10px;border-radius:50%;background:#555}
  .terms{left:11px;top:415px;width:191px;text-align:center;font-size:7.2px;line-height:9px;color:#555}
  .terms b{font-weight:400;color:#111}

  /* Main */
  .main{left:362px;background:linear-gradient(var(--orange),var(--orange-2))}
  .main .app-bar{background:var(--orange);border-bottom:3px solid #ff8f2a}
  .points{right:8px;top:49px;font-size:7px;font-weight:600;color:#fff}
  .menu{left:6px;top:51px;width:10px;height:8px}
  .main .frame{background:#ff9a1a}
  .draw-area{left:11px;top:90px;width:191px;height:149px;display:flex;align-items:center;justify-content:center;font-size:10.5px;font-weight:500;color:#333}
  .word-panel{left:11px;top:245px;width:191px;height:192px}
  .toggle{left:17px;top:259px;width:180px;height:36px;border:1.5px solid var(--green);border-radius:4px;background:#fff}
  .toggle-off{left:24px;top:272px;font-family:var(--head);font-weight:700;font-size:9px;color:#aaa}
  .toggle-on{left:106px;top:262px;width:88px;height:30px;border-radius:3px;background:var(--green);color:#fff;font-family:var(--head);font-weight:700;font-size:9px;text-align:center;line-height:30px}
  .tile{width:56px;height:33px;border-radius:4px;color:#fff;font-family:var(--head);font-weight:700;font-size:9px;text-align:center;line-height:33px}
  .giraffe{left:147px;top:334px;width:54px;height:103px;border-radius:4px;background:linear-gradient(#f6c35b,#f0a93a)}
  .results{left:17px;top:386px;width:180px;height:28px;border-radius:5px;background:linear-gradient(#ff8a1f,var(--orange-btn));color:#fff;font-family:var(--head);font-weight:700;font-size:9px;text-align:center;line-height:28px}

  /* Profile */
  .profile{left:633px;background:linear-gradient(var(--blue),var(--blue-2))}
  .profile .app-bar{background:var(--blue);border-bottom:3px solid var(--blue-line)}
  .back{left:7px;top:51px;width:6px;height:9px}
  .profile .frame{background:var(--blue-2)}
  .profile .panel{left:11px;top:90px;width:191px;height:347px}
  .avatar{left:80px;top:97px;width:54px;height:54px;border-radius:50%;background:radial-gradient(circle at 50% 40%,#d9b49a 0 30%,#6b4a38 55%,#d8d8d8 75%)}
  .cam{left:119px;top:134px;width:18px;height:18px;border-radius:50%;background:var(--yellow);border:2px solid #fff}
  .edit{left:11px;top:159px;width:191px;text-align:center;font-size:10.5px;font-weight:500;color:#333}
  .row-label{left:38px;font-size:6.2px;color:#666}
  .row-value{left:38px;font-size:7.5px;font-weight:600;color:#222}
  .row-icon{left:27px;width:8px;height:8px}
  .chev{left:184px;width:4px;height:6px}
  .divider{left:20px;width:174px;height:1px;background:#e4e4e4}
  .add-link{left:38px;top:334px;font-size:7.5px;font-weight:600;color:var(--orange)}
  .elephant{left:134px;top:384px;width:58px;height:53px;border-radius:8px;background:linear-gradient(#d5dde6,#aebcc9)}

  /* Stats */
  .stats{left:907px;background:linear-gradient(var(--purple),var(--purple-2))}
  .stats .app-bar{background:var(--purple);border-bottom:3px solid #b874fb}
  .user-dot{left:190px;top:45px;width:18px;height:18px;border-radius:50%;background:radial-gradient(circle at 50% 45%,#d7b39a 0 35%,#6f4e3d 60%,#eee 80%)}
  .stats .frame{background:var(--purple-soft)}
  .tab{top:90px;height:23px;border-radius:12px;color:#fff;font-size:8px;font-weight:500;text-align:center;line-height:23px}
  .rank{top:124px;height:48px;border-radius:4px;color:#fff;padding:11px 7px 0}
  .rank small{display:block;font-size:6.5px;font-weight:500}
  .rank strong{display:block;font-size:14.5px;font-weight:600;line-height:20px;white-space:nowrap}
  .curve{left:12px;top:183px;width:191px;height:149px;border-radius:5px}
  .recent{left:12px;top:341px;width:191px;height:97px;border-radius:5px}
  .card-title{position:absolute;left:7px;top:8px;font-size:10px;font-weight:500;color:#333}
  .word{position:absolute;left:7px;font-size:7.5px;color:#444}
  .word-line{position:absolute;left:7px;width:177px;height:1px;background:#e2e2e2}
</style>
</head>
<body>

<div class="board-label" style="left:87px">Login</div>
<div class="board-label" style="left:362px">Main Screen</div>
<div class="board-label" style="left:633px">Profile</div>
<div class="board-label" style="left:907px">BrivoTally</div>

<!-- Login -->
<section class="screen login">
  <span class="status-time">9:41</span>
  <svg class="status-icons" viewBox="0 0 40 10"><g fill="#222"><rect x="0" y="6" width="2" height="4"/><rect x="3" y="4" width="2" height="6"/><rect x="6" y="2" width="2" height="8"/><rect x="9" y="0" width="2" height="10"/><path d="M14 4a7 7 0 0 1 10 0l-1.3 1.3a5 5 0 0 0-7.4 0zM16.5 6.5a3.5 3.5 0 0 1 5 0L19 9z"/><rect x="28" y="1" width="11" height="7" rx="2"/></g></svg>
  <div class="frame"></div>
  <div class="panel card"></div>
  <div class="brand">Brivonest</div>
  <div class="tagline">Learn letters and words</div>
  <div class="hero" role="img" aria-label="Illustration of a bear reading a book on a grassy hill"></div>
  <div class="create">Create An Account</div>
  <div class="create-sub">Enter your email to sign up for this app</div>
  <div class="field">Email Address</div>
  <div class="btn-primary">Sign up with email</div>
  <div class="or">or continue with</div>
  <div class="btn-alt"><span class="mark"></span>Login with Quarnix</div>
  <div class="terms">By clicking continue, you agree to our<br><b>Terms of Service</b> and <b>Privacy Policy</b></div>
</section>

<!-- Main Screen -->
<section class="screen main">
  <div class="app-bar"></div>
  <span class="status-time">9:41</span>
  <svg class="status-icons" viewBox="0 0 40 10"><g fill="#222"><rect x="0" y="6" width="2" height="4"/><rect x="3" y="4" width="2" height="6"/><rect x="6" y="2" width="2" height="8"/><rect x="9" y="0" width="2" height="10"/><path d="M14 4a7 7 0 0 1 10 0l-1.3 1.3a5 5 0 0 0-7.4 0zM16.5 6.5a3.5 3.5 0 0 1 5 0L19 9z"/><rect x="28" y="1" width="11" height="7" rx="2"/></g></svg>
  <svg class="menu" viewBox="0 0 10 8"><g fill="#fff"><rect width="10" height="1.4"/><rect y="3.3" width="10" height="1.4"/><rect y="6.6" width="10" height="1.4"/></g></svg>
  <div class="app-title">Main Screen</div>
  <span class="points">16 Points</span>
  <div class="frame"></div>
  <div class="draw-area card">Drawing Area</div>
  <div class="word-panel card"></div>
  <div class="toggle"></div>
  <span class="toggle-off">Show all Words</span>
  <div class="toggle-on">Play all words</div>
  <div class="tile" style="left:17px;top:302px;background:var(--red)">Word 1</div>
  <div class="tile" style="left:78px;top:302px;background:var(--violet)">Word 2</div>
  <div class="tile" style="left:140px;top:302px;background:var(--yellow)">Word 3</div>
  <div class="tile" style="left:17px;top:341px;background:var(--green)">Word 1</div>
  <div class="tile" style="left:78px;top:341px;background:var(--cyan)">...</div>
  <div class="giraffe" role="img" aria-label="Illustration of a giraffe wearing glasses"></div>
  <div class="results">Show me the results</div>
</section>

<!-- Profile -->
<section class="screen profile">
  <div class="app-bar"></div>
  <span class="status-time">9:41</span>
  <svg class="status-icons" viewBox="0 0 40 10"><g fill="#222"><rect x="0" y="6" width="2" height="4"/><rect x="3" y="4" width="2" height="6"/><rect x="6" y="2" width="2" height="8"/><rect x="9" y="0" width="2" height="10"/><path d="M14 4a7 7 0 0 1 10 0l-1.3 1.3a5 5 0 0 0-7.4 0zM16.5 6.5a3.5 3.5 0 0 1 5 0L19 9z"/><rect x="28" y="1" width="11" height="7" rx="2"/></g></svg>
  <svg class="back" viewBox="0 0 6 9"><path d="M5 1 1.5 4.5 5 8" fill="none" stroke="#fff" stroke-width="1.4"/></svg>
  <div class="app-title">Profile</div>
  <div class="frame"></div>
  <div class="panel card"></div>
  <div class="avatar" role="img" aria-label="User profile photo"></div>
  <div class="cam"></div>
  <div class="edit">Edit profile image</div>

  <svg class="row-icon" style="top:193px" viewBox="0 0 8 8"><circle cx="4" cy="2.3" r="2" fill="#999"/><path d="M0 8a4 3 0 0 1 8 0z" fill="#999"/></svg>
  <span class="row-label" style="top:189px">Name</span>
  <span class="row-value" style="top:197px">Mara Quell</span>
  <svg class="chev" style="top:200px" viewBox="0 0 4 6"><path d="M.7.5 3.3 3 .7 5.5" fill="none" stroke="#222" stroke-width=".9"/></svg>
  <div class="divider" style="top:212px"></div>

  <svg class="row-icon" style="top:223px" viewBox="0 0 8 8"><circle cx="4" cy="2.3" r="2" fill="#999"/><path d="M0 8a4 3 0 0 1 8 0z" fill="#999"/></svg>
  <span class="row-label" style="top:219px">Username</span>
  <span class="row-value" style="top:227px">@username</span>
  <svg class="chev" style="top:230px" viewBox="0 0 4 6"><path d="M.7.5 3.3 3 .7 5.5" fill="none" stroke="#222" stroke-width=".9"/></svg>
  <div class="divider" style="top:245px"></div>

  <svg class="row-icon" style="top:258px" viewBox="0 0 8 8"><rect y="1" width="8" height="6" fill="#999"/><path d="M0 1.5 4 4.5 8 1.5" fill="none" stroke="#fff" stroke-width=".8"/></svg>
  <span class="row-label" style="top:254px">Email</span>
  <span class="row-value" style="top:262px">name@mailbox.com</span>
  <svg class="chev" style="top:265px" viewBox="0 0 4 6"><path d="M.7.5 3.3 3 .7 5.5" fill="none" stroke="#222" stroke-width=".9"/></svg>
  <div class="divider" style="top:279px"></div>

  <svg class="row-icon" style="top:290px" viewBox="0 0 8 8"><g fill="none" stroke="#999" stroke-width="1"><rect x=".5" y="3" width="4" height="3" rx="1.5" transform="rotate(-35 2.5 4.5)"/><rect x="3.5" y="2" width="4" height="3" rx="1.5" transform="rotate(-35 5.5 3.5)"/></g></svg>
  <span class="row-label" style="top:286px">Links</span>
  <span class="row-value" style="top:298px">sitepage.net</span>
  <span class="row-value" style="top:311px">myspot.net</span>
  <span class="row-value" style="top:323px">yourspot.net</span>
  <span class="add-link">+Add link</span>
  <div class="divider" style="top:348px"></div>

  <svg class="row-icon" style="top:359px" viewBox="0 0 8 8"><rect y="1" width="8" height="6" rx="1" fill="#999"/><rect x="1.2" y="2.5" width="2" height="2" fill="#fff"/><rect x="4" y="3" width="3" height=".8" fill="#fff"/></svg>
  <span class="row-label" style="top:355px">Bio</span>
  <span class="row-value" style="top:363px">A description of this user.</span>
  <svg class="chev" style="top:366px" viewBox="0 0 4 6"><path d="M.7.5 3.3 3 .7 5.5" fill="none" stroke="#222" stroke-width=".9"/></svg>
  <div class="elephant" role="img" aria-label="Illustration of an elephant reading with glasses"></div>
</section>

<!-- BrivoTally -->
<section class="screen stats">
  <div class="app-bar"></div>
  <span class="status-time">9:41</span>
  <svg class="status-icons" viewBox="0 0 40 10"><g fill="#222"><rect x="0" y="6" width="2" height="4"/><rect x="3" y="4" width="2" height="6"/><rect x="6" y="2" width="2" height="8"/><rect x="9" y="0" width="2" height="10"/><path d="M14 4a7 7 0 0 1 10 0l-1.3 1.3a5 5 0 0 0-7.4 0zM16.5 6.5a3.5 3.5 0 0 1 5 0L19 9z"/><rect x="28" y="1" width="11" height="7" rx="2"/></g></svg>
  <svg class="menu" viewBox="0 0 10 8"><g fill="#fff"><rect width="10" height="1.4"/><rect y="3.3" width="10" height="1.4"/><rect y="6.6" width="10" height="1.4"/></g></svg>
  <div class="app-title">BrivoTally</div>
  <div class="user-dot" role="img" aria-label="User avatar photo"></div>
  <div class="frame"></div>
  <div class="tab" style="left:15px;width:57px;background:var(--cyan)">Ranking</div>
  <div class="tab" style="left:76px;width:78px;background:#eab7f7">Correct Words</div>
  <div class="tab" style="left:158px;width:43px;background:#eab7f7">Todo..</div>
  <div class="rank" style="left:12px;width:117px;background:var(--yellow)"><small>Total Ranking</small><strong>1st Place of 100</strong></div>
  <div class="rank" style="left:134px;width:84px;background:var(--green)"><small>Daily Ranking</small><strong>10th Place</strong></div>

  <div class="curve card">
    <span class="card-title">Learning curve</span>
    <svg style="position:absolute;left:0;top:0" width="191" height="149" viewBox="0 0 191 149">
      <g stroke="#e2e2e2" stroke-width=".7">
        <line x1="7" y1="30" x2="184" y2="30"/><line x1="7" y1="49" x2="184" y2="49"/><line x1="7" y1="68" x2="184" y2="68"/><line x1="7" y1="86" x2="184" y2="86"/><line x1="7" y1="105" x2="184" y2="105"/><line x1="7" y1="124" x2="184" y2="124"/>
      </g>
      <g font-family="Poppins, sans-serif" font-size="6.2" fill="#666">
        <text x="7" y="41">100 words per day</text><text x="7" y="60">50 words per day</text>
        <text x="7" y="78">......</text><text x="7" y="97">......</text><text x="7" y="116">......</text>
        <text x="7" y="136">Nov</text><text x="30" y="136">23</text><text x="50" y="136">24</text><text x="70" y="136">25</text><text x="89" y="136">26</text><text x="110" y="136">27</text><text x="130" y="136">28</text><text x="151" y="136">29</text><text x="171" y="136">30</text>
      </g>
      <polyline points="8,125 40,121 66,106 74,109 108,87 118,89 134,70 143,80 153,61 164,68 175,39" fill="none" stroke="#c06cf8" stroke-width="1.6" stroke-linejoin="round"/>
      <circle cx="175" cy="39" r="2.2" fill="#d9a3fc"/>
    </svg>
  </div>

  <div class="recent card">
    <span class="card-title">Recently learned words</span>
    <span class="word" style="top:27px">El</span>
    <div class="word-line" style="top:39px"></div>
    <span class="word" style="top:43px">ELA</span>
    <div class="word-line" style="top:55px"></div>
    <span class="word" style="top:59px">Lorem</span>
    <div class="word-line" style="top:71px"></div>
    <span class="word" style="top:75px">Lorem</span>
  </div>
</section>

</body>
</html>
```